Business Cards for new orthopaedic surgery practice

My husband and I are starting our own orthopaedic surgery practice. We are looking for a business card that is uniform, but one will have my name/title and the other will have his. You can just create one design with my name on it for now. But when I choose your design as the winning design I will ask that you add another copy with his name/title.

We are looking for classy, simple, elite all in one. We like dark blues/a little gold/yellow. Something that goes with our logo. We want our logo incorporated. Here is all the info you need:
Business name: RV Bone & Vitality Center
Location: 38517 North Willowmere Ave
Maple Hollow, FL 33590
Phone: 954-218-4063
Fax: 954-582-7341
Email: info@myrvbonecare.example

Names: Lydia Vance, M.D.
Board Certified Hand and Upper Extremity Surgeon

Ebo Dansu, M.D.
Board Certified Hip & Knee Replacement/General Orthopaedic Surgeon

Can decide what you want to put on the back. Maybe a slogan:
Steady Hands. Built Around You

I am just going to upload our logo. The only thing is if we select you as the winning design, the location, and phone numbers may change. We will need your help to update that once fully solidified.

Industry/Entity Type

Medical

Contact Information for Business Card

Colors
0054AA
0677BA
7BADD7
CADEEF
E8F1F8
0094D4
00A9DD
6FCCEA
C7EBF8
E9F6FB

Requirements
Must have
• class, appeal,
Should not have
• We want to air on the side of masculine if we are looking at masculine vs. feminine feel. But we still want it classy, sophisticated, and something we will love

```html
<!DOCTYPE html>
<html lang="en">
<head>
<meta charset="utf-8">
<title>RV Bone &amp; Vitality Center — Business Card</title>
<link rel="stylesheet" href="https://fonts.googleapis.com/css2?family=Marcellus&family=Montserrat:wght@400;500;700&family=Merriweather:wght@700&display=swap">
<style>
  :root {
    --backdrop: #dedfe2;
    --navy: #273374;
    --gold: #d6ad4f;
    --gold-light: #f3dc8d;
    --gold-deep: #b08633;
    --cyan: #1bb8dc;
    --white: #ffffff;
  }
  * { margin: 0; padding: 0; box-sizing: border-box; }
  html, body { width: 1200px; height: 1129px; overflow: hidden; }
  body {
    background: var(--backdrop);
    position: relative;
    font-family: "Montserrat", sans-serif;
  }
  .card {
    position: absolute;
    left: 211px;
    width: 779px;
    height: 450px;
    background: var(--navy);
    border-radius: 36px;
    overflow: hidden;
  }
  .card--front { top: 94px; }
  .card--back { top: 585px; }

  .brand-name {
    font-family: "Marcellus", serif;
    color: var(--gold);
    font-weight: 400;
  }
  .card--front .brand-name {
    position: absolute;
    left: 0; right: 0;
    top: 212px;
    text-align: center;
    font-size: 46px;
    letter-spacing: 1px;
  }
  .card--front .brand-mark {
    position: absolute;
    left: 50%;
    top: 120px;
    width: 60px; height: 60px;
    margin-left: -30px;
    border: 3px solid var(--gold);
    border-radius: 50%;
  }
  .card--back .brand-name {
    position: absolute;
    left: 26px;
    top: 60px;
    font-size: 28px;
    line-height: 1.2;
  }

  .doctor {
    position: absolute;
    right: 30px;
    top: 80px;
    text-align: right;
  }
  .doctor__name {
    color: var(--gold);
    font-weight: 700;
    font-size: 29px;
    letter-spacing: 0.3px;
  }
  .doctor__title {
    color: var(--white);
    font-weight: 500;
    font-size: 16.5px;
    margin-top: 6px;
  }

  .contacts {
    position: absolute;
    left: 30px;
    top: 268px;
    list-style: none;
  }
  .contacts li {
    display: flex;
    align-items: center;
    height: 30.7px;
    color: var(--white);
    font-size: 19px;
  }
  .contacts svg { width: 18px; height: 18px; margin-right: 9px; fill: var(--cyan); }

  .address {
    position: absolute;
    right: 30px;
    top: 322px;
    text-align: right;
    color: var(--white);
    font-size: 19px;
    line-height: 31px;
  }

  .footer-band {
    position: absolute;
    left: 0; bottom: 0;
    width: 779px; height: 39px;
  }
  .tagline {
    position: absolute;
    left: 31px;
    bottom: 10px;
    font-family: "Merriweather", serif;
    font-weight: 700;
    font-size: 17px;
    color: var(--navy);
  }
</style>
</head>
<body>

<section class="card card--front">
  <span class="brand-mark"></span>
  <h1 class="brand-name">RV Bone &amp; Vitality Center</h1>
</section>

<section class="card card--back">
  <h2 class="brand-name">RV Bone &amp;<br>Vitality Center</h2>

  <div class="doctor">
    <p class="doctor__name">LYDIA VANCE, M.D</p>
    <p class="doctor__title">Hand and Upper Extremity Surgery</p>
  </div>

  <ul class="contacts">
    <li><svg viewBox="0 0 24 24"><path d="M2 9c0-3 4-5 10-5s10 2 10 5v2h-5V9c-1-1-3-1.5-5-1.5S8 8 7 9v2H2z M6 12h12l2 8H4z"/></svg>954-218-4063</li>
    <li><svg viewBox="0 0 24 24"><path d="M6 2h12v5H6z M3 8h18v9h-3v5H6v-5H3z M8 14v6h8v-6z"/></svg>954-582-7341</li>
    <li><svg viewBox="0 0 24 24"><path d="M2 5h20l-10 8z M2 7l10 8 10-8v12H2z"/></svg>info@myrvbonecare.example</li>
    <li><svg viewBox="0 0 24 24"><circle cx="12" cy="12" r="10"/><path d="M2 12h20M12 2c-4 4-4 16 0 20M12 2c4 4 4 16 0 20" stroke="#273374" stroke-width="1.5" fill="none"/></svg>www.myrvbonecare.example</li>
  </ul>

  <p class="address">38517 North Willowmere Ave<br>Maple Hollow, FL 33590</p>

  <svg class="footer-band" viewBox="0 0 779 39" preserveAspectRatio="none" aria-hidden="true">
    <defs>
      <linearGradient id="goldBand" x1="0" x2="1" y1="0" y2="0">
        <stop offset="0" stop-color="#b8913f"/>
        <stop offset="0.35" stop-color="#f3dc8d"/>
        <stop offset="0.65" stop-color="#f1d98a"/>
        <stop offset="1" stop-color="#b08633"/>
      </linearGradient>
    </defs>
    <rect x="0" y="0" width="779" height="39" fill="url(#goldBand)"/>
    <path d="M372 0 Q382 0 388 12 Q394 22 408 22 L779 22 L779 0 Z" fill="#273374"/>
    <path d="M386 1 L779 1 L779 14 L404 14 Q394 14 390 8 Z" fill="#1bb8dc"/>
  </svg>
  <p class="tagline">Steady Hands. Built Around You</p>
</section>

</body>
</html>
```